Design a Website in Wordpress for an Australian Health Training Company in Health related courses

We require a WORDPRESS based Website (due to add on's we need to use for third party software) to replace our old site.
We offer national face to face delivery in medical reception, terminology and also administration.
The website will have around 6 pages and the ability to describe our main 6 courses (perhaps on the Courses page this may be tabs opening up to details for example?)
I have attached a previous sample of a Joomla site which was being developed (please do not feel you have to copy this - but I am just giving it as a sample - copying would be boring). But it gives an idea of look/feel and colours which may be suitable. Open to other ideas though.
I will provide some of the content, but would like the ability to finish the content myself.
Images and graphics are important. While a few medical photos re great - don't be tempted to us all pictures of doctors and nurses (although a couple would be good) - these are administrative courses so general corporate, eye catching visionary pictures of people in general are great. A medical type picture is also fine.
THE BOOKING system - will be via an ADD ON which will occur at the end of the project and is supplied by a third party software company (our student management system). This project will include up to 2 hours working with the Tech guys from the third party software to enable the ADD ON. If this ADD ON requires more time, we will pay hourly (although I do not expect it will).
Target Market(s)
Mostly a female market, many mature aged women target 25-45 yrs. Mixture of medical/health and corporate. Maybe a bit of mums returning to work and corporate inspiration.
Industry/Entity Type
It Company
Coding
Coded - Design and coding required
Number of Pages Required
5+ page
Requirements
Must have
- Wordpress
- Great graphics
- Interesting
- professional and clean
- Enquiry section (info Pak)
- Should have a University feel to it - Education
- Pages
- Home Page - About Us - Recruitment -Courses - Class Schedule - Traineeships Queensland Funding - Latest News Blog - Corporate Training- Contact us

```html
<!DOCTYPE html>
<html lang="en">
<head>
<meta charset="utf-8">
<title>Harwood Institute of Training</title>
<link href="https://fonts.googleapis.com/css2?family=Cinzel:wght@400;600;700&family=Open+Sans:ital,wght@0,400;0,600;0,700;1,400&family=Raleway:wght@500;600;700&display=swap" rel="stylesheet">
<style>
:root{
  --blue:#0b4ea2;
  --blue-dark:#083c80;
  --navy:#0d3f86;
  --orange:#f7a046;
  --orange-deep:#f28a1e;
  --grey-band:#ebebeb;
  --text:#666;
  --text-dark:#333;
  --white:#fff;
  --ink:#222;
}
*{box-sizing:border-box;margin:0;padding:0}
html,body{width:1200px;height:2875px;overflow:hidden}
body{font-family:"Open Sans",Arial,sans-serif;color:var(--text);background:var(--white);position:relative}

/* top bar */
.topbar{position:absolute;top:0;left:0;width:1200px;height:38px;background:var(--blue);color:var(--white)}
.topbar .phone{position:absolute;left:148px;top:10px;font-size:13px;font-weight:600;display:flex;align-items:center;gap:8px}
.topbar .search{position:absolute;left:465px;top:7px;width:172px;height:24px;background:var(--white);font-size:9px;color:#999;padding:6px 8px}
.topbar .search-btn{position:absolute;left:637px;top:7px;width:24px;height:24px;background:var(--blue-dark);border:1px solid #fff3;display:flex;align-items:center;justify-content:center}
.topbar .socials{position:absolute;right:150px;top:0;display:flex;height:38px}
.topbar .socials span{width:34px;height:38px;border-left:1px solid #ffffff40;display:flex;align-items:center;justify-content:center}
.topbar .socials i{width:12px;height:12px;background:var(--white);display:block}

/* header */
.header{position:absolute;top:38px;left:0;width:1200px;height:92px;background:var(--white)}
.header .links a{position:absolute;top:36px;font-size:11px;color:#555;text-transform:uppercase;text-align:center;line-height:15px;text-decoration:none}
.btn-head{position:absolute;left:893px;width:142px;height:30px;color:var(--white);font-size:11px;font-weight:700;text-transform:uppercase;display:flex;align-items:center;padding-left:12px;gap:16px}
.btn-enrol{top:14px;background:var(--blue)}
.btn-info{top:48px;background:var(--ink)}

.logo-box{position:absolute;left:146px;top:38px;width:184px;height:182px;background:var(--white);box-shadow:0 3px 8px #0003;z-index:5;display:flex;flex-direction:column;align-items:center;padding-top:18px;gap:14px}
.logo-box .name{font-family:"Cinzel",Georgia,serif;font-weight:700;font-size:15px;line-height:18px;color:var(--navy);text-align:center}
.logo-box .mark{width:64px;height:64px;background:var(--navy)}

/* nav */
.mainnav{position:absolute;top:130px;left:0;width:1200px;height:47px;background:linear-gradient(var(--orange),var(--orange-deep))}
.mainnav a{position:absolute;top:15px;color:var(--white);font-family:"Raleway",sans-serif;font-weight:700;font-size:13.5px;text-transform:uppercase;text-decoration:none}

/* hero */
.hero{position:absolute;top:177px;left:0;width:1200px;height:443px;
  background:linear-gradient(100deg,#9c7a63 0%,#d9c6b6 9%,#eef0f2 20%,#f8f9fb 38%,#eceef1 50%,#d6d9de 58%,#7f8fa6 67%,#3c4c66 75%,#8a6c58 84%,#c7ccd3 92%,#eef0f3 100%)}
.hero h1{position:absolute;left:150px;top:158px;font-family:"Cinzel",Georgia,serif;font-weight:600;color:var(--navy);font-size:38px;line-height:42px}
.hero h1 .l1{font-size:33px}
.dots{position:absolute;display:flex;gap:6px}
.dots i{width:16px;height:16px;border-radius:50%;background:var(--white);display:block}
.dots i:first-child{background:transparent;border:2px solid var(--white)}

/* welcome */
.welcome{position:absolute;top:620px;left:0;width:1200px;height:260px;text-align:center}
.welcome h2{font-family:"Cinzel",Georgia,serif;font-weight:400;color:var(--navy);font-size:27px;line-height:36px;margin-top:36px}
.welcome p{width:800px;margin:18px auto 0;font-size:12.5px;line-height:24px;color:#777}

.section-title{font-family:"Cinzel",Georgia,serif;font-weight:400;font-size:26px;text-align:center;letter-spacing:1px}
.section-title::after{content:"";display:block;width:50px;height:3px;background:var(--blue);margin:8px auto 0}

/* courses */
.courses{position:absolute;top:880px;left:0;width:1200px;height:332px;background:var(--grey-band)}
.courses .section-title{margin-top:40px;color:var(--text-dark)}
.course{position:absolute;display:flex;align-items:center;gap:16px;font-size:15px;text-transform:uppercase;color:#444;line-height:23px}
.course .ic{width:76px;height:76px;border-radius:50%;background:var(--blue);border:5px solid var(--white);box-shadow:0 0 0 1px #ccc;display:flex;align-items:center;justify-content:center;flex:none}

/* why */
.why{position:absolute;top:1212px;left:0;width:1200px;height:398px}
.why .section-title{margin-top:36px;color:var(--text-dark)}
.why .section-title::after{display:none}
.why-card{position:absolute;top:102px;width:173px;height:252px;border:1px solid #ddd;background:var(--white);text-align:center;overflow:hidden}
.why-card .photo{height:118px}
.why-card h3{font-size:15px;font-weight:400;color:var(--blue);margin:12px 0 6px}
.why-card p{font-size:10px;line-height:14px;color:#777;padding:0 10px;height:70px;overflow:hidden}

/* info pack */
.infopack{position:absolute;top:1610px;left:0;width:1200px;height:226px;
  background:linear-gradient(115deg,#6b4a33 0%,#8a6448 14%,#5e4636 26%,#6f6c6a 40%,#9a9894 50%,#4f5257 62%,#35383d 78%,#5a4a3e 100%)}
.infopack h2{font-family:"Cinzel",Georgia,serif;font-weight:400;color:var(--white);font-size:22px;text-align:center;margin-top:30px}
.infopack h2::after{content:"";display:block;width:46px;height:3px;background:var(--white);margin:8px auto 0}
.field{position:absolute;width:233px;height:35px;background:linear-gradient(#fff,#eee);font-size:11px;color:#999;padding:11px 12px}
.submit{position:absolute;width:233px;height:35px;background:var(--orange);color:var(--white);font-weight:700;font-size:14px;text-align:center;line-height:35px}

/* blogs */
.blogs{position:absolute;top:1836px;left:0;width:1200px;height:426px}
.blogs .section-title{margin-top:36px;color:var(--navy)}
.blogs .section-title::after{display:none}
.blog-card{position:absolute;top:86px;width:290px;height:284px;border:1px solid #ddd;background:var(--white);padding:10px}
.blog-card .photo{height:136px;position:relative}
.blog-card .date{position:absolute;left:76px;bottom:-12px;background:var(--blue);color:var(--white);font-size:12px;font-weight:600;padding:5px 14px}
.blog-card h3{font-size:16px;font-weight:600;color:var(--orange-deep);margin-top:24px}
.blog-card p{font-size:11.5px;line-height:16px;color:#888;margin-top:4px}
.blog-card .more{font-size:12px;color:#333;margin-top:8px}

/* testimonials */
.testimonials{position:absolute;top:2262px;left:0;width:1200px;height:290px;background:linear-gradient(100deg,#f9b15a,#f28a1e)}
.testimonials .notch{position:absolute;left:580px;top:0;width:0;height:0;border-left:20px solid transparent;border-right:20px solid transparent;border-top:18px solid var(--white)}
.testimonials h2{font-family:"Raleway",sans-serif;font-weight:600;font-size:21px;color:var(--white);text-align:center;margin-top:60px}
.avatar{position:absolute;left:183px;top:115px;width:88px;height:88px;border-radius:50%;background:linear-gradient(160deg,#3b2a22 0%,#8a5e45 40%,#d9b49a 70%,#f1e6dc 100%);border:4px solid var(--white)}
.person{position:absolute;left:285px;top:132px;color:var(--white);font-size:15px;line-height:24px}
.person .role{color:#fde6c8;font-size:13px}
.divider{position:absolute;left:436px;top:100px;width:1px;height:130px;background:#ffffff70}
.quote{position:absolute;left:488px;top:110px;width:530px;color:var(--white);font-style:italic;font-size:13px;line-height:28px}
.qmark{position:absolute;font-family:Georgia,serif;font-size:40px;line-height:40px;color:var(--white);font-style:normal}
.testimonials .dots{left:558px;top:252px}
.testimonials .dots i{width:15px;height:15px}

/* footer */
.footer{position:absolute;top:2552px;left:0;width:1200px;height:266px;background:var(--blue);color:var(--white)}
.footer h4{position:absolute;top:48px;font-size:14px;font-weight:600;text-transform:uppercase}
.footer .col{position:absolute;top:84px;font-size:11.5px;line-height:18px}
.contact-row{display:flex;gap:10px;margin-bottom:12px}
.post .t{font-size:13px;color:#dde8f7}
.post .d{font-size:10px;line-height:14px}
.post .dt{font-size:10px;color:#c6d6ee;margin:2px 0 14px}
.input{width:220px;height:32px;background:var(--white);color:#999;font-size:11px;padding:9px 10px;margin-bottom:10px}
.click{width:100px;height:34px;background:var(--orange);font-size:12px;font-weight:700;text-align:center;line-height:34px}
.social-row{display:flex;align-items:center;gap:8px;margin-bottom:14px;font-size:13px}
.social-row i{width:22px;height:22px;border-radius:50%;border:1px solid var(--white);display:block}
.bottom{position:absolute;top:2818px;left:0;width:1200px;height:57px;background:var(--blue-dark);color:#c6d6ee;font-size:11px;text-align:center;line-height:57px}
</style>
</head>
<body>

<div class="topbar">
  <div class="phone">
    <svg width="14" height="14" viewBox="0 0 24 24"><path fill="#fff" d="M6.6 10.8a15 15 0 006.6 6.6l2.2-2.2a1 1 0 011-.25 11.4 11.4 0 003.6.6 1 1 0 011 1V20a1 1 0 01-1 1A17 17 0 013 4a1 1 0 011-1h3.5a1 1 0 011 1c0 1.25.2 2.45.6 3.6a1 1 0 01-.25 1z"/></svg>
    1800 555 0142
  </div>
  <div class="search">Search here</div>
  <div class="search-btn"><svg width="11" height="11" viewBox="0 0 12 12"><circle cx="5" cy="5" r="3.5" stroke="#fff" stroke-width="1.6" fill="none"/><path d="M7.6 7.6L11 11" stroke="#fff" stroke-width="1.8"/></svg></div>
  <div class="socials"><span><i></i></span><span><i></i></span><span><i></i></span><span><i></i></span></div>
</div>

<div class="header">
  <div class="links">
    <a style="left:380px">About<br>Us</a>
    <a style="left:470px">Class<br>Schedule</a>
    <a style="left:608px">Traineeships<br>Queensland Funding</a>
    <a style="left:775px">Latest News<br>Blog</a>
  </div>
  <div class="btn-head btn-enrol">
    <svg width="12" height="12" viewBox="0 0 12 12"><path d="M10 10L2 2M2 2v6M2 2h6" stroke="#fff" stroke-width="2" fill="none"/></svg>Enrol Now
  </div>
  <div class="btn-head btn-info">
    <svg width="14" height="14" viewBox="0 0 14 14"><circle cx="7" cy="7" r="7" fill="#fff"/><rect x="6" y="6" width="2" height="5" fill="#222"/><rect x="6" y="3" width="2" height="2" fill="#222"/></svg>Info Pack
  </div>
</div>

<div class="logo-box">
  <div class="name">HARWOOD INSTITUTE<br>OF TRAINING</div>
  <div class="mark"></div>
</div>

<nav class="mainnav">
  <a style="left:380px">Home Page</a>
  <a style="left:498px">Recruitment</a>
  <a style="left:635px">Courses</a>
  <a style="left:736px">Corporate Training</a>
  <a style="left:930px">Contact Us</a>
</nav>

<section class="hero" role="img" aria-label="Photo of a trainer presenting to a group of seated adult students in a bright office classroom">
  <h1><span class="l1">WE PROVIDE HEALTH</span><br>EDUCATION TRAINING</h1>
  <div class="dots" style="left:558px;top:408px"><i></i><i></i><i></i><i></i></div>
</section>

<section class="welcome">
  <h2>WELCOME TO<br>HARWOOD INSTITUTE OF TRAINING</h2>
  <p>Harwood is Australia's Leading Provider of Educational, Training and Support Services for the Medical and Dental industry - enabling students to be immediately skilled and 'Job Ready' for a career in Health. Harwood is a Registered Training Organisation offering specialised Medical Administration Training in over 15 locations Australia wide. Harwood have trained thousands of students the required knowledge and skills to become successful health care administrators</p>
</section>

<section class="courses">
  <h2 class="section-title">OUR COURSES</h2>
  <div class="course" style="left:175px;top:102px">
    <span class="ic"><svg width="30" height="30" viewBox="0 0 24 24"><path d="M9 3h6M10 3v6L4 20h16L14 9V3" stroke="#fff" stroke-width="2" fill="none"/><path d="M7 15h10l3 5H4z" fill="#fff"/></svg></span>
    Medical Reception<br>&amp; Terminology
  </div>
  <div class="course" style="left:492px;top:102px">
    <span class="ic"><svg width="30" height="30" viewBox="0 0 24 24"><path d="M5 3v6a5 5 0 0010 0V3M10 14v3a4 4 0 008 0v-4" stroke="#fff" stroke-width="2" fill="none"/><circle cx="18" cy="11" r="2" fill="#fff"/></svg></span>
    Medical<br>Terminology
  </div>
  <div class="course" style="left:772px;top:102px">
    <span class="ic"><svg width="30" height="30" viewBox="0 0 24 24"><circle cx="12" cy="12" r="9" fill="#fff"/><path d="M8 7c2 1 1 3 3 4s0 4 2 5M15 5c-1 2 1 3 3 4" stroke="#0b4ea2" stroke-width="2" fill="none"/></svg></span>
    Harwood<br>Online
  </div>
  <div class="course" style="left:175px;top:200px">
    <span class="ic"><svg width="30" height="30" viewBox="0 0 24 24"><rect x="3" y="7" width="18" height="13" rx="2" fill="#fff"/><path d="M9 7V4h6v3" stroke="#fff" stroke-width="2" fill="none"/><rect x="3" y="12" width="18" height="2" fill="#0b4ea2"/></svg></span>
    Cert III Business<br>Administration
  </div>
  <div class="course" style="left:492px;top:200px">
    <span class="ic"><svg width="32" height="32" viewBox="0 0 24 24"><rect x="2" y="6" width="20" height="12" rx="2" fill="#fff"/><g fill="#0b4ea2"><rect x="4" y="8" width="2" height="2"/><rect x="7" y="8" width="2" height="2"/><rect x="10" y="8" width="2" height="2"/><rect x="13" y="8" width="2" height="2"/><rect x="16" y="8" width="2" height="2"/><rect x="4" y="11" width="2" height="2"/><rect x="7" y="11" width="2" height="2"/><rect x="10" y="11" width="2" height="2"/><rect x="13" y="11" width="2" height="2"/><rect x="16" y="11" width="2" height="2"/><rect x="6" y="14" width="12" height="2"/></g></svg></span>
    Keyboard and<br>Typing
  </div>
  <div class="course" style="left:772px;top:200px">
    <span class="ic"><svg width="30" height="30" viewBox="0 0 24 24"><rect x="3" y="6" width="7" height="14" rx="3" fill="#fff"/><rect x="14" y="6" width="7" height="14" rx="3" fill="#fff"/><rect x="9" y="9" width="6" height="4" fill="#fff"/></svg></span>
    Confidentiality
  </div>
</section>

<section class="why">
  <h2 class="section-title">WHY HARWOOD INSTITUTE ?</h2>
  <div class="why-card" style="left:148px">
    <div class="photo" role="img" aria-label="Close-up of a compass needle pointing to the word quality" style="background:linear-gradient(140deg,#0a1c36 0%,#1d4f8c 35%,#6fa3d8 55%,#24578f 70%,#0c2444 100%)"></div>
    <h3>Quality</h3>
    <p>Harwood delivers quality, effective training facilitated by industry leaders. Just ask our students who rate us on average of 4.7 out of 5</p>
  </div>
  <div class="why-card" style="left:330px">
    <div class="photo" role="img" aria-label="Hands of a team joining coloured gears on a table" style="background:linear-gradient(140deg,#3a2418 0%,#7a4d34 30%,#c79a7a 48%,#5f8a8a 60%,#8a5a3e 75%,#2f211a 100%)"></div>
    <h3>Experience</h3>
    <p>Harwood is Australia's largest and leading providers of nationally recognised training in health administration – training from over 17 locations</p>
  </div>
  <div class="why-card" style="left:512px">
    <div class="photo" role="img" aria-label="Wooden letter blocks spelling value on a workbench" style="background:linear-gradient(140deg,#b4713a 0%,#e0a86d 30%,#f3e2c8 48%,#d08a4a 62%,#5d7890 82%,#3e5468 100%)"></div>
    <h3>Value</h3>
    <p>Our innovative teaching approach allows us to deliver exceptional training at affordable prices with no hidden extras.</p>
  </div>
  <div class="why-card" style="left:694px">
    <div class="photo" role="img" aria-label="Soft grey image of an eye symbol for recognition" style="background:radial-gradient(circle at 55% 55%,#6f7f92 0%,#b7c2cf 22%,#e3e8ee 45%,#f7f9fb 100%)"></div>
    <h3>Industry Recognised</h3>
    <p>Harwood work hand in hand with industry to develop our core programme and consolidate the programme annually to keep the programme fresh and</p>
  </div>
  <div class="why-card" style="left:876px">
    <div class="photo" role="img" aria-label="Hand holding a paper sign with a great job message" style="background:linear-gradient(180deg,#1f4e8c 0%,#3d6aa6 22%,#ffffff 40%,#f2f4f7 70%,#e2c9b4 100%)"></div>
    <h3>Great Job Results</h3>
    <p>Harwood students get jobs! Our focus is to create job-ready students who are mentored to achieve their goals. Harwood also provide a recruitment</p>
  </div>
</section>

<section class="infopack" role="img" aria-label="Dark background photo of a laptop keyboard on a wooden desk">
  <h2>EMAIL me an Info Pack</h2>
  <div class="field" style="left:242px;top:88px">Name</div>
  <div class="field" style="left:485px;top:88px">Email</div>
  <div class="field" style="left:728px;top:88px">Course</div>
  <div class="field" style="left:242px;top:132px">State</div>
  <div class="field" style="left:485px;top:132px">Mobile</div>
  <div class="submit" style="left:728px;top:132px">SUBMIT</div>
</section>

<section class="blogs">
  <h2 class="section-title">LATEST BLOGS</h2>
  <article class="blog-card" style="left:146px">
    <div class="photo" role="img" aria-label="Smiling woman working at a laptop" style="background:linear-gradient(110deg,#f4f1ec 0%,#e8d8c8 18%,#c8382f 40%,#a8261f 52%,#e9d3c2 66%,#f6f2ec 80%,#d9cbb9 100%)"><span class="date">02 MAY 2016</span></div>
    <h3>Aculis facilisis massa</h3>
    <p>Etiam eu urna Sed porta Suspendisse quam leo molestie sed luctus quis feugiat in pede Fusce tellus Sed metus augue</p>
    <div class="more">Read More</div>
  </article>
  <article class="blog-card" style="left:455px">
    <div class="photo" role="img" aria-label="Students seated in a lecture hall listening to a teacher" style="background:linear-gradient(180deg,#e9eef4 0%,#bcd0e6 30%,#5f87b8 48%,#c9a58a 62%,#f0e2d4 76%,#7a8aa0 100%)"><span class="date">02 MAY 2016</span></div>
    <h3>Aculis facilisis massa</h3>
    <p>Etiam eu urna Sed porta Suspendisse quam leo molestie sed luctus quis feugiat in pede Fusce tellus Sed metus augue</p>
    <div class="more">Read More</div>
  </article>
  <article class="blog-card" style="left:765px">
    <div class="photo" role="img" aria-label="Group of students studying together at a table" style="background:linear-gradient(120deg,#4a3328 0%,#8c5e42 25%,#d8b597 45%,#6a4c3b 60%,#c7a282 78%,#efe3d6 100%)"><span class="date">02 MAY 2016</span></div>
    <h3>Aculis facilisis massa</h3>
    <p>Etiam eu urna Sed porta Suspendisse quam leo molestie sed luctus quis feugiat in pede Fusce tellus Sed metus augue</p>
    <div class="more">Read More</div>
  </article>
</section>

<section class="testimonials">
  <div class="notch"></div>
  <h2>TESTIMONIALS</h2>
  <div class="avatar" role="img" aria-label="Portrait photo of the student giving the testimonial"></div>
  <div class="person">Clare Hadley<br><span class="role">City Location Area</span></div>
  <div class="divider"></div>
  <span class="qmark" style="left:458px;top:104px">&ldquo;</span>
  <p class="quote">I want to say a huge thank you for the course and knowledge I come away with. I have secured a fantastic job after my first application! Such good value for money too! I would highly recommend it. I'm a mature age person so it's never too late to up -skill yourself to get what you deserve &rdquo;</p>
  <div class="dots"><i></i><i></i><i></i><i></i></div>
</section>

<footer class="footer">
  <h4 style="left:152px">Contact Us</h4>
  <div class="col" style="left:152px;width:240px">
    <div class="contact-row">
      <svg width="14" height="18" viewBox="0 0 14 18" style="flex:none"><path d="M7 1a6 6 0 00-6 6c0 4 6 10 6 10s6-6 6-10a6 6 0 00-6-6z" stroke="#fff" stroke-width="1.5" fill="none"/><circle cx="7" cy="7" r="2" fill="#fff"/></svg>
      <span>12 Kestrel Lane Suite 4 Milbrook,<br>QLD 4012 Voice 07 5550 1188</span>
    </div>
    <div class="contact-row">
      <svg width="14" height="14" viewBox="0 0 24 24" style="flex:none"><path fill="#fff" d="M6.6 10.8a15 15 0 006.6 6.6l2.2-2.2a1 1 0 011-.25 11.4 11.4 0 003.6.6 1 1 0 011 1V20a1 1 0 01-1 1A17 17 0 013 4a1 1 0 011-1h3.5a1 1 0 011 1c0 1.25.2 2.45.6 3.6a1 1 0 01-.25 1z"/></svg>
      <span>Phone:+61 7 5550 1234</span>
    </div>
    <div class="contact-row">
      <svg width="15" height="12" viewBox="0 0 15 12" style="flex:none"><rect x="1" y="1" width="13" height="10" stroke="#fff" fill="none"/><path d="M1 1l6.5 5L14 1" stroke="#fff" fill="none"/></svg>
      <span>info@harwoodtraining.example</span>
    </div>
  </div>

  <h4 style="left:427px">Latest Posts</h4>
  <div class="col" style="left:427px;width:220px">
    <div class="post"><div class="t">In iaculis facilisis massa Etiam</div><div class="d">Nam cursus Morbi ut mi Nullam enim</div><div class="dt">25 May 2016</div></div>
    <div class="post"><div class="t">Fusce tellus Sed</div><div class="d">pulvinar eu ante Integer orci tellus tristique vitae consequat nec</div><div class="dt">25 May 2016</div></div>
  </div>

  <h4 style="left:690px">Enquiry Now</h4>
  <div class="col" style="left:690px">
    <div style="font-size:10px;margin-bottom:10px">Excepteur sint occaecat cupidatat non proa</div>
    <div class="input">Your Name</div>
    <div class="input">Email address</div>
    <div class="click">CLICK HERE</div>
  </div>

  <h4 style="left:970px">Social</h4>
  <div class="col" style="left:970px;top:82px">
    <div class="social-row"><i></i>Community</div>
    <div class="social-row"><i></i>Updates</div>
    <div class="social-row"><i></i>Circles</div>
    <div class="social-row"><i></i>Video Channel</div>
  </div>
</footer>
<div class="bottom">© 2016 Company Name All right reserved Term of Use</div>

</body>
</html>
```